** Wanted ** Wordpress web design for scaffolding rental and construction company

We need a website design and must be functional to show a basic overview of what our company offers as a service. We have a domain name and a logo but we need web design. This web site should have another scaffolding rental page for construction and renovation as well as a quote section where customers can enter their personal information and also upload photos. The site% 26quot; www.brindlework.com% 26quot; should be intuitive, clear and classy ... The logo must be found on the site in several ways.

Target Market(s)

Professional and no professional

Coding

Coded - Design and coding required

Number of Pages Required

3 page

Font styles to use
Serif
Sans Serif
Decorative
Script

Requirements
Must have
• Our logo
Nice to have
• Slogan:% 26quot; The height% 26 # 224; port% 26 # 233; e hand% 26quot;

```html
<!DOCTYPE html>
<html lang="en">
<head>
<meta charset="utf-8">
<title>Brindlework — Scaffolding &amp; Construction</title>
<link rel="stylesheet" href="https://fonts.googleapis.com/css2?family=Barlow:wght@400;500;600;700&family=Rubik:wght@400;500&display=swap">
<style>
:root{
  --orange:#e8711c;
  --black:#000;
  --ink:#222;
  --text:#555;
  --light:#f4f4f4;
  --line:#dcdcdc;
  --white:#fff;
}
*{box-sizing:border-box;margin:0;padding:0}
html,body{width:1200px;height:3561px;overflow:hidden}
body{position:relative;font-family:"Barlow",sans-serif;color:var(--ink);background:var(--white)}
.abs{position:absolute}
.center{left:0;width:1200px;text-align:center}

/* header */
.site-header{top:0;left:0;width:1200px;height:123px;background:var(--black)}
.brand{display:flex;align-items:center;gap:10px;font-family:"Barlow",sans-serif;font-weight:700;color:var(--orange);letter-spacing:1px}
.brand-mark{background:var(--orange)}
.site-header .brand{position:absolute;left:110px;top:42px;font-size:30px}
.site-header .brand-mark{width:22px;height:22px}
.main-nav{position:absolute;top:52px;left:0;width:1200px;height:20px}
.main-nav a{position:absolute;font-size:13.5px;font-weight:500;color:var(--white);text-decoration:none;font-family:"Rubik",sans-serif}
.main-nav a.active{color:var(--orange)}

/* hero */
.hero{top:123px;left:0;width:1200px;height:704px;background:linear-gradient(180deg,#2c5a74 0%,#3f6a7a 35%,#8a6a44 62%,#d6882c 72%,#2a1c10 85%,#120c08 100%)}
.hero-title{top:171px;font-size:72px;font-weight:700;color:var(--white);text-shadow:0 3px 8px rgba(0,0,0,.5)}
.hero-sub{top:272px;font-size:27px;font-weight:500;color:var(--white)}
.dots{top:763px;left:575px;display:flex;gap:7px}
.dots span{width:12px;height:12px;border-radius:50%;background:var(--white)}
.dots span.on{background:var(--orange)}
.hero-wave{left:0;top:797px}

/* welcome */
.welcome{top:827px;left:0;width:1200px;height:683px;background:var(--light)}
.section-title{font-weight:700;font-size:38px;color:var(--ink)}
.welcome .section-title{top:874px}
.welcome-text{top:946px;font-family:"Rubik",sans-serif;font-size:13.5px;line-height:32px;color:var(--text)}
.service-card{top:1049px;width:309px;height:394px;background:var(--white);border:1px solid #e2e2e2;box-shadow:0 1px 4px rgba(0,0,0,.08);text-align:center}
.service-icon{position:absolute;left:87px;top:26px;width:134px;height:134px;border-radius:50%;background:var(--orange);display:flex;align-items:center;justify-content:center}
.service-icon.dark{background:#333}
.service-card h3{position:absolute;top:176px;left:0;width:100%;font-family:"Rubik",sans-serif;font-weight:500;font-size:22px;color:var(--ink)}
.service-card p{position:absolute;top:218px;left:24px;width:259px;font-family:"Rubik",sans-serif;font-size:12.5px;line-height:25.5px;color:var(--text)}
.btn-outline{position:absolute;top:317px;left:96px;width:116px;height:44px;border:1px solid var(--orange);border-radius:2px;font-family:"Rubik",sans-serif;font-size:15px;font-weight:500;color:var(--orange);display:flex;align-items:center;justify-content:center}
.btn-outline.dark{border-color:#333;color:#333}

/* what we do */
.about-box{top:1573px;left:110px;width:980px;height:461px;background:var(--white);box-shadow:0 0 6px rgba(232,113,28,.18)}
.about-photo{position:absolute;left:0;top:0;width:482px;height:461px;background:linear-gradient(120deg,#3a6f9c 0%,#7aa4c6 35%,#c9a23a 60%,#3d4c6c 100%)}
.about-box h2{position:absolute;left:523px;top:40px;font-size:38px;font-weight:700;color:var(--ink)}
.rule{height:3px;width:66px;background:var(--orange)}
.about-box .rule{position:absolute;left:523px;top:102px}
.about-box p{position:absolute;left:523px;top:128px;width:420px;font-family:"Rubik",sans-serif;font-size:13.5px;line-height:26.5px;color:var(--text);text-align:justify}
.btn-solid{background:var(--orange);color:var(--white);font-family:"Rubik",sans-serif;font-weight:500;display:flex;align-items:center;justify-content:center;border-radius:2px}
.about-box .btn-solid{position:absolute;left:523px;top:371px;width:137px;height:47px;font-size:17px}

/* video band */
.video-band{top:2099px;left:0;width:1200px;height:503px;background:linear-gradient(180deg,#3f5a6c 0%,#5a6168 35%,#7a5030 65%,#2a1a10 100%)}
.video-title{top:2258px;font-size:40px;font-weight:700;color:var(--white)}
.video-sub{top:2319px;font-size:27px;font-weight:500;color:var(--white)}
.play{left:560px;top:2381px;width:80px;height:80px;border-radius:50%;border:3px solid var(--white);background:#111;display:flex;align-items:center;justify-content:center}

/* contact */
.contact-title{top:2650px}
.contact-rule{left:567px;top:2710px}
.contact-photo{left:143px;top:2745px;width:373px;height:373px;border-radius:50%;background:linear-gradient(180deg,#4a7fc4 0%,#9ab4d4 45%,#e8a860 75%,#3a2a22 100%)}
.contact-badge{left:390px;top:3028px;width:86px;height:86px;border-radius:50%;background:var(--white);border:3px solid var(--orange);display:flex;align-items:center;justify-content:center}
.contact-badge span{width:30px;height:30px;border-radius:50%;background:var(--orange)}
.field{height:46px;border:1px solid #cfcfcf;font-family:"Rubik",sans-serif;font-size:13px;color:#444;padding:14px 14px 0}
.contact-submit{left:565px;top:3023px;width:146px;height:50px;font-size:18px}

/* footer */
.site-footer{top:3172px;left:0;width:1200px;height:389px;background:var(--black)}
.site-footer .brand{position:absolute;left:0;width:1200px;top:3228px;justify-content:center;font-size:40px}
.site-footer .brand-mark{width:28px;height:28px}
.footer-nav a{position:absolute;top:3358px;font-family:"Rubik",sans-serif;font-size:13.5px;font-weight:500;color:var(--white);text-decoration:none}
.social{top:3410px;width:60px;height:60px;border:1px solid #9a9a9a;border-radius:50%;display:flex;align-items:center;justify-content:center}
.copyright{top:3502px;font-family:"Rubik",sans-serif;font-size:13px;color:#ddd}
</style>
</head>
<body>

<header class="site-header abs">
  <div class="brand"><span class="brand-mark"></span>BRINDLEWORK</div>
  <nav class="main-nav">
    <a class="active" style="left:528px">HOME</a>
    <a style="left:608px">ABOUT US</a>
    <a style="left:715px">SERVICES</a>
    <a style="left:820px">PROJECTS</a>
    <a style="left:928px">NEWS</a>
    <a style="left:1008px">CONTACT US</a>
  </nav>
</header>

<section class="hero abs" role="img" aria-label="Silhouettes of workers on scaffolding against a sunset sky"></section>
<h1 class="hero-title abs center">BRINDLEWORK</h1>
<p class="hero-sub abs center">SED UT PERSPICIATIS UNDE OMNIS ISTE NATUS ERROR SIT</p>
<div class="dots abs"><span></span><span class="on"></span><span></span></div>
<svg class="hero-wave abs" width="1200" height="31" viewBox="0 0 1200 31"><path d="M520 31 C560 22 580 4 600 4 C620 4 640 22 680 31 Z" fill="#f4f4f4"/></svg>

<section class="welcome abs"></section>
<h2 class="section-title abs center" style="top:874px">WELCOME TO BRINDLEWORK</h2>
<p class="welcome-text abs center">Sed ut perspiciatis unde omnis iste natus error sit voluptatem accusantium doloremque laudantium, totam rem &nbsp;ipsa quae<br>ab illo inventore veritatis et quasi architecto beatae vitae dicta sunt explicabo.</p>

<article class="service-card abs" style="left:110px">
  <div class="service-icon">
    <svg width="70" height="80" viewBox="0 0 70 80" fill="none" stroke="#fff" stroke-width="3"><rect x="4" y="6" width="62" height="16" rx="3"/><rect x="24" y="22" width="22" height="50" rx="4"/><circle cx="35" cy="32" r="5"/><circle cx="35" cy="48" r="5"/></svg>
  </div>
  <h3>Services 01</h3>
  <p>Sed ut perspiciatis unde omnis iste natus error sit voluptatem accusantium dolorem vitae dicta sunt explicabo.</p>
  <div class="btn-outline">Read More</div>
</article>
<article class="service-card abs" style="left:445px">
  <div class="service-icon dark">
    <svg width="74" height="74" viewBox="0 0 74 74" fill="none" stroke="#fff" stroke-width="3"><path d="M14 70V8M26 70V8M14 8h54M14 18h54M60 18v16M4 70h66"/><rect x="38" y="56" width="24" height="14"/><path d="M56 34l4 8 4-8"/></svg>
  </div>
  <h3>Services 02</h3>
  <p>Sed ut perspiciatis unde omnis iste natus error sit voluptatem accusantium dolorem vitae dicta sunt explicabo.</p>
  <div class="btn-outline dark">Read More</div>
</article>
<article class="service-card abs" style="left:780px">
  <div class="service-icon">
    <svg width="78" height="78" viewBox="0 0 78 78" fill="none" stroke="#fff" stroke-width="3"><path d="M33 6h12l2 10 8 4 9-6 8 8-6 9 4 8 10 2v12l-10 2-4 8 6 9-8 8-9-6-8 4-2 10H33l-2-10-8-4-9 6-8-8 6-9-4-8-10-2V33l10-2 4-8-6-9 8-8 9 6 8-4z"/><circle cx="39" cy="39" r="11"/></svg>
  </div>
  <h3>Services 03</h3>
  <p>Sed ut perspiciatis unde omnis iste natus error sit voluptatem accusantium dolorem vitae dicta sunt explicabo.</p>
  <div class="btn-outline">Read More</div>
</article>

<section class="about-box abs">
  <div class="about-photo" role="img" aria-label="Worker in a hard hat welding on yellow scaffolding"></div>
  <h2>WHAT WE DO</h2>
  <div class="rule"></div>
  <p>Sed ut perspiciatis unde omnis iste natus error sit voluptatem accusantium doloremque laudantium, totam rem aperiam, eaque ipsa quae ab illo inventore veritatis et quasi architecto beatae vitae dicta sunt explicabo. Nemo enim ipsam voluptatem quia voluptas sit aspernatur aut odit aut fugit, sed quia consequuntur eos qui ratione voluptatem sequi nesciunt.Neque porro quisquam est, qui dolorem ipsum quia dolor sit amet, consectetur, adipisci velit, sed magnam aliquam quaerat voluptatem.</p>
  <div class="btn-solid">READ MORE</div>
</section>

<section class="video-band abs" role="img" aria-label="Silhouetted construction crew working on a steel frame at dusk"></section>
<h2 class="video-title abs center">SED UT PERSPICIATIS UNDE</h2>
<p class="video-sub abs center">ISTE NATUS ERROR SIT VOLUPTATEM ACCUSANTIUM DOLOREMQUE</p>
<div class="play abs"><svg width="26" height="28" viewBox="0 0 26 28"><path d="M4 2l20 12-20 12z" fill="#fff"/></svg></div>

<h2 class="section-title contact-title abs center">CONTACT US</h2>
<div class="rule contact-rule abs"></div>
<div class="contact-photo abs" role="img" aria-label="Tower cranes against a sunset sky"></div>
<div class="contact-badge abs"><span></span></div>
<form>
  <div class="field abs" style="left:565px;top:2787px;width:251px">First Name :</div>
  <div class="field abs" style="left:828px;top:2787px;width:252px">Last Name :</div>
  <div class="field abs" style="left:565px;top:2842px;width:251px">Email :</div>
  <div class="field abs" style="left:828px;top:2842px;width:252px">Phone :</div>
  <div class="field abs" style="left:565px;top:2898px;width:515px;height:99px">Message :</div>
  <div class="btn-solid contact-submit abs">SUBMIT</div>
</form>

<footer class="site-footer abs"></footer>
<div class="brand"><span class="brand-mark"></span>BRINDLEWORK</div>
<nav class="footer-nav">
  <a style="left:319px">HOME</a>
  <a style="left:399px">ABOUT US</a>
  <a style="left:506px">SERVICES</a>
  <a style="left:610px">PROJECTS</a>
  <a style="left:719px">NEWS</a>
  <a style="left:798px">CONTACT US</a>
</nav>
<div class="social abs" style="left:390px" aria-label="Social link"></div>
<div class="social abs" style="left:462px" aria-label="Social link"></div>
<div class="social abs" style="left:535px" aria-label="Social link"></div>
<div class="social abs" style="left:606px" aria-label="Social link"></div>
<div class="social abs" style="left:676px" aria-label="Social link"></div>
<div class="social abs" style="left:748px" aria-label="Email">
  <svg width="18" height="14" viewBox="0 0 18 14" fill="none" stroke="#fff" stroke-width="1.5"><rect x="1" y="1" width="16" height="12" rx="1"/><path d="M1 2l8 6 8-6"/></svg>
</div>
<p class="copyright abs center">© Copyrights 2020-Brindlework.All Rights Reserved.</p>

<style>
.site-footer + .brand{position:absolute;left:0;width:1200px;top:3228px;justify-content:center;font-size:40px}
.site-footer + .brand .brand-mark{width:28px;height:28px}
</style>
</body>
</html>
```